Investment company needing business card

We are wanting a business card which looks sharp and easy on the eye. We are thinking of having a business card with the logo embossed on it, to really make it stand out. We will only have a small amount of information of the business card, person's name, position, email address and phone number

Contact Information for Business Card

Danielle Frost
Executive Assistant
+64 21 473 5162
danielf@harwickpartners.co.nz

Requirements
Must have
• Embossed logo
Should not have
• Not to be busy

```html
<!DOCTYPE html>
<html lang="en">
<head>
<meta charset="utf-8">
<title>Harwick Partners – Business Card</title>
<link rel="stylesheet" href="https://fonts.googleapis.com/css2?family=Open+Sans:wght@400;700&display=swap">
<style>
  :root {
    --backdrop: #e8e6e3;
    --card: #ffffff;
    --brand-green: #2bb673;
    --brand-grey: #9a9a9a;
    --text-grey: #6b6b6b;
    --on-green: #ffffff;
  }
  * { margin: 0; padding: 0; box-sizing: border-box; }
  html, body {
    width: 1200px; height: 997px; overflow: hidden;
    background: var(--backdrop);
    font-family: "Open Sans", Arial, sans-serif;
  }
  .cards { position: relative; width: 1200px; height: 997px; }
  .card {
    position: absolute; top: 344px;
    width: 540px; height: 309px;
    background: var(--card);
    box-shadow: 0 2px 6px rgba(0,0,0,0.12);
    overflow: hidden;
  }
  .card--front { left: 40px; }
  .card--back { left: 620px; }

  .card__wave { position: absolute; inset: 0; }

  .brand {
    position: absolute; display: flex; align-items: center; gap: 8px;
    color: var(--brand-green); font-weight: 700;
    letter-spacing: 1px; text-transform: uppercase;
  }
  .brand__mark { background: var(--brand-green); display: block; }
  .card--front .brand { top: 58px; left: 34px; font-size: 19px; }
  .card--front .brand__mark { width: 26px; height: 26px; }
  .card--back .brand { top: 136px; left: 50%; transform: translateX(-50%); font-size: 26px; white-space: nowrap; }
  .card--back .brand__mark { width: 34px; height: 34px; }

  .person { position: absolute; top: 150px; left: 40px; }
  .person__name {
    color: var(--brand-green); font-weight: 700; font-size: 14px;
    text-transform: uppercase; letter-spacing: 0.3px;
  }
  .person__role { color: var(--text-grey); font-size: 12.5px; margin-top: 1px; }

  .contact {
    position: absolute; right: 22px; top: 96px;
    list-style: none; text-align: right;
    color: var(--on-green); font-size: 12px; line-height: 18px;
    white-space: nowrap;
  }
  .contact__item { display: flex; justify-content: flex-end; align-items: center; gap: 6px; }
  .contact__icon { width: 10px; height: 10px; flex: none; }
</style>
</head>
<body>
<main class="cards">

  <section class="card card--front" aria-label="Business card front">
    <svg class="card__wave" viewBox="0 0 540 309" width="540" height="309" aria-hidden="true">
      <path d="M40 309 C190 305 250 100 390 74 C450 64 500 61 540 60 V309 Z" fill="var(--brand-green)"/>
      <path d="M0 300 C50 294 100 293 140 289 S250 64 400 48 S510 42 540 41" fill="none" stroke="var(--brand-grey)" stroke-width="8" stroke-linecap="round"/>
      <path d="M80 309 C220 303 275 110 400 86 C460 76 510 73 540 72" fill="none" stroke="#ffffff" stroke-width="1.5"/>
    </svg>

    <div class="brand"><span class="brand__mark"></span>Harwick Partners</div>

    <div class="person">
      <p class="person__name">Danielle Frost</p>
      <p class="person__role">Executive Assistant</p>
    </div>

    <ul class="contact">
      <li class="contact__item">+64 21 473 5162
        <svg class="contact__icon" viewBox="0 0 10 10" aria-hidden="true"><path d="M2 1 L4 1 L4.6 3 L3.4 4 C4 5.3 4.8 6.1 6 6.6 L7 5.4 L9 6 L9 8 C5 8.5 1.5 5 2 1 Z" fill="currentColor"/></svg>
      </li>
      <li class="contact__item">danielf@harwickpartners.co.nz
        <svg class="contact__icon" viewBox="0 0 10 10" aria-hidden="true"><rect x="0.5" y="2" width="9" height="6" fill="none" stroke="currentColor"/><path d="M0.5 2 L5 5.5 L9.5 2" fill="none" stroke="currentColor"/></svg>
      </li>
      <li class="contact__item">www.harwickpartners.co.nz
        <svg class="contact__icon" viewBox="0 0 10 10" aria-hidden="true"><circle cx="5" cy="5" r="4.3" fill="none" stroke="currentColor"/><ellipse cx="5" cy="5" rx="1.8" ry="4.3" fill="none" stroke="currentColor"/><path d="M0.7 5 H9.3" stroke="currentColor"/></svg>
      </li>
    </ul>
  </section>

  <section class="card card--back" aria-label="Business card back">
    <div class="brand"><span class="brand__mark"></span>Harwick Partners</div>
  </section>

</main>
</body>
</html>
```